Talvoro bonds (Surety bond broker)

We are a broker of surety bonds, we need a presentation and a flyer with fresh design. Our core values are reliable, on time and customized service. We want to transmit to our clients, they can leave on us the process of underwriting and issuing a surety bond, so they can focus on their business with no distractions.

Font styles to use
Sans Serif
Other font styles liked:

Requirements
Must have
• Visually attractive.
Main Message: Fast service issuing and underwriting surety bonds, reliable, nos surprises, we are always one step ahead, customized and personalized bonding solutions.
Nice to have
• Have short version for the flyer, and extended version for the presentation.
Should not have
• We already have a logo (attached), maintain colors

```html
<!DOCTYPE html>
<html lang="es">
<head>
<meta charset="utf-8">
<title>Talvoro Seguros y Fianzas – Tríptico</title>
<link href="https://fonts.googleapis.com/css2?family=Montserrat:wght@400;500;600;700;800&display=swap" rel="stylesheet">
<style>
:root{
  --green:#6aa43a;
  --green-soft:#a9cf8a;
  --black:#0c0c0c;
  --white:#ffffff;
  --text-grey:#4d4d4d;
  --stage:#ececec;
  --light:#cfcfcf;
}
*{box-sizing:border-box;margin:0;padding:0}
html,body{width:720px;height:1200px;overflow:hidden}
body{background:var(--stage);font-family:"Montserrat",sans-serif;position:relative}
.spread{position:absolute;left:20px;width:680px;height:560px;display:grid;grid-template-columns:repeat(3,1fr);box-shadow:0 6px 18px rgba(0,0,0,.18)}
.spread--outside{top:25px}
.spread--inside{top:615px}
.panel{position:relative;overflow:hidden;padding:22px 16px}
.panel--white{background:var(--white);color:var(--text-grey)}
.panel--black{background:var(--black);color:var(--white)}
.accent{color:var(--green)}
.heading{font-size:15px;font-weight:600;line-height:1.2}
.heading-rule{width:14px;height:2px;background:var(--green);margin:8px 0 10px}
.body-copy{font-size:7.3px;line-height:1.45}
.body-copy p{margin-bottom:7px}

/* brand */
.brand{display:flex;align-items:center;gap:5px}
.brand-mark{width:8px;height:8px;background:var(--green)}
.brand-name{font-size:22px;font-weight:500;color:var(--green);letter-spacing:.5px;line-height:1}
.brand-tag{font-size:5.5px;letter-spacing:1.5px;color:var(--white);text-align:right;margin-top:2px}

/* panel 1 outside */
.about-photo{position:absolute;left:0;bottom:0;width:100%;height:220px;background:linear-gradient(135deg,#2f3a45,#5b6c7a 55,#c9cfd4);border-top-right-radius:100% 70%}
.about-blob{position:absolute;border-radius:50%;background:var(--green-soft);opacity:.85}
.about-blob--a{width:60px;height:52px;left:122px;top:318px}
.about-blob--b{width:36px;height:32px;left:168px;top:346px}
.about-curve{position:absolute;left:0;bottom:0}

/* partners */
.partners-title{font-size:10px;font-weight:700;color:var(--green);text-align:center;margin-top:6px}
.partners-circle{width:170px;height:170px;border-radius:50%;background:#f2f2f2;margin:14px auto 0;outline:1.5px solid var(--green);outline-offset:6px;display:grid;grid-template-columns:repeat(2,48px);justify-content:center;align-content:center;gap:10px 14px}
.partner-badge{height:16px;border-radius:3px;background:var(--light)}
.partner-badge--round{width:16px;border-radius:50%;justify-self:center}
.contact{margin-top:34px}
.contact .brand{margin-bottom:14px}
.contact-title{font-size:11px;font-weight:500;margin-bottom:9px}
.contact-person{margin-bottom:6px}
.contact-name{font-size:7.5px;font-weight:700;color:var(--green)}
.contact-line{display:flex;align-items:center;gap:5px;font-size:7.3px;margin-top:2px}
.contact-dot{width:6px;height:6px;border:1px solid var(--green);border-radius:50%;flex:none}

/* cover */
.cover .brand{justify-content:flex-end;margin-top:4px}
.cover-photo{width:196px;height:196px;border-radius:50%;margin:22px auto 0;background:radial-gradient(circle at 40% 40%,#6d8fb8,#243f66 60%,#172a45);outline:1.5px solid var(--green);outline-offset:6px}
.cover-tagline{margin-top:52px;text-align:right;font-size:16px;font-weight:700;line-height:1.2}
.cover-rule{width:16px;height:2px;background:var(--green);margin:10px 0 0 auto}
.cover-web{margin-top:10px;text-align:right;font-size:8px;letter-spacing:2px}

/* inside */
.services{list-style:none;margin-top:4px}
.services li{font-size:7.3px;font-weight:600;line-height:1.35;margin-bottom:6px;padding-left:10px;position:relative}
.services li::before{content:"✓";position:absolute;left:0;color:var(--green)}
.services small{display:block;font-size:5.5px;font-weight:400;color:#bbb}

.product{display:flex;align-items:center;gap:8px;margin-top:14px}
.product-circle{width:58px;height:58px;border-radius:50%;background:var(--green);border:2px solid var(--white);outline:1px solid var(--green);flex:none;display:flex;flex-direction:column;align-items:center;justify-content:center;gap:4px;font-size:6.5px;font-weight:600}
.product-list{list-style:none;font-size:6.3px;line-height:1.35;border-bottom:1px solid var(--green);padding-bottom:3px;flex:1}
.product-list .tick{color:var(--green);font-weight:600}
.product-list .tick::before{content:"✓ "}
.product-list .bullet{padding-left:6px}
.product-list .bullet::before{content:"• "}

.special h3{font-size:8px;font-weight:600;color:var(--green);margin:12px 0 4px}
.call-band{position:absolute;left:16px;right:16px;bottom:54px;background:var(--green);color:var(--white);font-size:15px;font-weight:800;padding:5px 8px;letter-spacing:.5px}
.call-phone{position:absolute;left:16px;bottom:26px;font-size:18px;font-weight:800;color:var(--black)}
</style>
</head>
<body>

<section class="spread spread--outside">
  <div class="panel panel--white about">
    <h2 class="heading" style="color:#222">¿Quiénes <span class="accent">somos?</span></h2>
    <div class="heading-rule"></div>
    <div class="body-copy">
      <p>Talvoro bonds, somos un grupo de jóvenes emprendedores, con amplia experiencia en el sector afianzador.</p>
      <p>Estamos convencidos de que nuestro principal diferenciador es la pasión por el servicio.</p>
      <p>Nuestra prioridad es el éxito de cada uno de nuestros clientes, nos aseguramos de que el “trámite” de fianzas deje de ser un “trámite” y se convierta en la llave del éxito para cada uno de nuestros fiados y beneficiarios.</p>
      <p>Buscamos siempre tener relaciones estrechas y de largo plazo con todos nuestros “stakeholders”. Por lo que nos rodeamos del mejor talento en el sector para garantizar a nuestros clientes un servicio personalizado, en tiempo y confiable.</p>
    </div>
    <div class="about-blob about-blob--a"></div>
    <div class="about-blob about-blob--b"></div>
    <div class="about-photo" role="img" aria-label="Fotografía: ejecutivo hablando por teléfono frente a monitores con gráficas financieras"></div>
  </div>

  <div class="panel panel--black partners">
    <h2 class="partners-title">Nuestro Socios de Negocio</h2>
    <div class="partners-circle" aria-label="Afianzadoras socias">
      <div class="partner-badge"></div><div class="partner-badge partner-badge--round"></div>
      <div class="partner-badge"></div><div class="partner-badge partner-badge--round"></div>
      <div class="partner-badge"></div><div class="partner-badge"></div>
      <div class="partner-badge"></div><div class="partner-badge"></div>
      <div class="partner-badge"></div><div class="partner-badge partner-badge--round"></div>
    </div>
    <div class="contact">
      <div>
        <div class="brand"><span class="brand-mark"></span><span class="brand-name">TALVORO</span></div>
        <div class="brand-tag" style="text-align:left;padding-left:13px">SEGUROS Y FIANZAS</div>
      </div>
      <h3 class="contact-title" style="margin-top:12px">Contacto</h3>
      <div class="contact-person">
        <div class="contact-name">Marina Solís</div>
        <div class="contact-line"><span class="contact-dot"></span>msolis@talvoro.com</div>
        <div class="contact-line"><span class="contact-dot"></span>55 0123 4501</div>
      </div>
      <div class="contact-person">
        <div class="contact-name">Lucía Prado</div>
        <div class="contact-line"><span class="contact-dot"></span>lprado@talvoro.com</div>
        <div class="contact-line"><span class="contact-dot"></span>55 0123 4502</div>
      </div>
      <div class="contact-person">
        <div class="contact-name">Diego Varela</div>
        <div class="contact-line"><span class="contact-dot"></span>dvarela@talvoro.com</div>
        <div class="contact-line"><span class="contact-dot"></span>55 0123 4503</div>
      </div>
      <div class="contact-line" style="margin-top:8px"><span class="contact-dot"></span>www.talvoro.com</div>
    </div>
  </div>

  <div class="panel panel--black cover">
    <div>
      <div class="brand"><span class="brand-mark"></span><span class="brand-name">TALVORO</span></div>
      <div class="brand-tag">SEGUROS Y FIANZAS</div>
    </div>
    <div class="cover-photo" role="img" aria-label="Fotografía: equipo celebrando frente a pantallas de mercado financiero"></div>
    <p class="cover-tagline">Tu éxito..<br><span class="accent">nuestra pasión</span></p>
    <div class="cover-rule"></div>
    <p class="cover-web">www.tal<span class="accent">voro</span>.com</p>
  </div>
</section>

<section class="spread spread--inside">
  <div class="panel panel--black offer">
    <h2 class="heading">Nuestra oferta <span class="accent">de valor</span></h2>
    <div class="heading-rule"></div>
    <div class="body-copy">
      <p><span class="accent">Para nuestros fiados</span>, nos aseguramos de que el proceso de emisión de fianzas sea <span class="accent">claro, rápido y sencillo.</span> Dando una asesoría personalizada y seguimiento puntual a cada solicitud.</p>
      <p>Sabemos la importancia de tener una fianza en tiempo y sin errores, por lo que nos empeñamos en siempre ir un paso adelante, permitiendo que nuestros clientes se despreocupen del proceso de afianzamiento y logren todos sus objetivos.</p>
      <p><span class="accent">Para nuestros beneficiarios</span>, trabajamos solo con las mejores afianzadoras del país y garantizamos que todos nuestros clientes cuenten con una garantía confiable, que les permita concluir sus proyectos con la tranquilidad de que tienen un respaldo confiable. Nuestro compromiso es siempre mitigar los riesgos y nunca dejar desprotegidos a nuestros clientes.</p>
    </div>
    <h2 class="heading" style="margin-top:10px">Nuestros <span class="accent">Servicios</span></h2>
    <div class="heading-rule"></div>
    <ul class="services">
      <li>Asesoría personalizada para la obtención de Líneas de Afianzamiento</li>
      <li>Emisión y administración de fianzas.<small>(Fidelidad, Administrativas, Judiciales, Crédito y Fideicomisos)</small></li>
      <li>Diseño, implementación y gestión de esquemas de afianzamiento.</li>
      <li>Asesoría en riesgos para contratos de obra, suministro y proveeduría.</li>
      <li>Colocación de fianzas internacionales y reaseguro.</li>
      <li>Asesoría legal en proceso de reclamación de fianzas.</li>
      <li>Esquemas de afianzamiento masivos.</li>
    </ul>
  </div>

  <div class="panel panel--black products">
    <h2 class="heading">Productos en <span class="accent">Fianzas</span></h2>
    <div class="heading-rule"></div>
    <div class="product">
      <div class="product-circle"><svg width="16" height="16" viewBox="0 0 16 16"><circle cx="8" cy="8" r="6" fill="none" stroke="#fff" stroke-width="1.6"/></svg>Fidelidad</div>
      <ul class="product-list"><li class="tick">Colectiva</li><li class="tick">Individual</li></ul>
    </div>
    <div class="product">
      <div class="product-circle"><svg width="16" height="16" viewBox="0 0 16 16"><rect x="3" y="3" width="10" height="10" fill="none" stroke="#fff" stroke-width="1.6"/></svg>Judicial</div>
      <ul class="product-list">
        <li class="tick">Penales</li><li class="bullet">Libertad provisional</li><li class="bullet">Condena provisional</li><li class="bullet">Reparación del daño</li><li class="bullet">Sanción pecuniaria</li>
        <li class="tick">No Penales</li><li class="bullet">Daños y prejuicios</li><li class="bullet">Pensión alimenticia</li><li class="bullet">Laboral</li>
      </ul>
    </div>
    <div class="product">
      <div class="product-circle" style="font-size:5.6px"><svg width="16" height="16" viewBox="0 0 16 16"><path d="M3 8l3 3 7-7" fill="none" stroke="#fff" stroke-width="1.8"/></svg>Administrativas</div>
      <ul class="product-list">
        <li class="tick">Obra y Proveeduría</li><li class="bullet">Cumplimiento</li><li class="bullet">Anticipo</li><li class="bullet">Buena Calidad</li><li class="bullet">Contingencias Laborales</li>
        <li class="tick">Arrendamiento</li><li class="tick">Contingencias ambientales</li><li class="tick">Fiscales</li>
      </ul>
    </div>
    <div class="product">
      <div class="product-circle"><svg width="18" height="14" viewBox="0 0 18 14"><rect x="1" y="1" width="16" height="12" rx="2" fill="none" stroke="#fff" stroke-width="1.5"/><line x1="1" y1="5" x2="17" y2="5" stroke="#fff" stroke-width="1.5"/></svg>Crédito</div>
      <ul class="product-list">
        <li class="tick">Compra venta</li><li class="tick">Suministro</li><li class="bullet">Eléctrica Nacional</li><li class="bullet">Estaciones de Servicio</li><li class="bullet">Petrolera Estatal</li><li class="bullet">Red Aeroportuaria</li><li class="tick">Otras Crédito</li>
      </ul>
    </div>
  </div>

  <div class="panel panel--white special">
    <h2 class="heading" style="color:#222">Productos <span class="accent">Especiales</span></h2>
    <div class="heading-rule"></div>
    <div class="body-copy">
      <h3>Flujo Garantizado</h3>
      <p>Es una fianza con la que se constituye un fondo colectivo para productos masivos que permite darle viabilidad financiera a tu empresa, proporcionándole el flujo constante de recursos para cubrir posibles pérdidas por quebrantos de créditos o cuentas por cobrar no liquidadas por sus clientes.</p>
      <h3>Esquemas de Proveedores</h3>
      <p>Esquema diseñado para grandes beneficiarios, que permite proteger los recursos invertidos en proyectos de construcción y adquisición de bienes o prestación de servicios, garantizando las obligaciones que se derivan de estos a cargo de sus proveedores o contratistas.</p>
      <p>Este programa permite la fácil administración de fianzas, previniendo un procedimiento ágil para la ejecución y cobro de las garantías que se emitan dentro del esquema.</p>
      <h3>Programa de garantías de fianzas para PyMEs</h3>
      <p>Con este programa puedes incrementar la línea de afianzamiento, gracias a que Fondafin aporta 50% de las garantías requeridas en fianzas hasta por 30 millones de pesos</p>
    </div>
    <div class="call-band">CALL FOR INFO</div>
    <div class="call-phone">+52 55 0123 4503</div>
  </div>
</section>

</body>
</html>
```